Business Recognition Design

We need a design for a recognition to be given to business leaders in our community.
The recognition shall be made on a brass plaque on wood panel background (picture attached, please use it as a background), and all drawing must be in vectors and only one color (black).
It should also have a logo on the top and signature on the right bottom.
The text is enclosed in DOC file.
Updates

Reason: just to be able to find the best solution

Reason: None of the suggestion is good enough. Logo in general is too big in comparison with the rest of the plate.

Industry/Entity Type

Business

Requirements
Must have
• - standard Windows font (or possibility to install the same font on Windows), as the name on the recognition shall be printed in the same font
Nice to have
• - some graphic element (in curves) representing achievements in business
- should look great :)

```html
<!DOCTYPE html>
<html lang="de">
<head>
<meta charset="utf-8">
<title>Auszeichnung – Unternehmer Deutschlands 2013</title>
<link rel="stylesheet" href="https://fonts.googleapis.com/css2?family=Arimo:wght@400;700&display=swap">
<style>
  :root {
    --backdrop: #3b3b3b;
    --wood-dark: #4a2814;
    --wood-mid: #6e4026;
    --wood-light: #87553a;
    --brass-deep: #c99a24;
    --brass-mid: #e2bb45;
    --brass-light: #f6dc7a;
    --ink: #111111;
    --screw-dark: #8a6410;
    --screw-light: #fbe08a;
  }
  * { box-sizing: border-box; margin: 0; padding: 0; }
  html, body {
    width: 1200px; height: 832px; overflow: hidden;
    background: var(--backdrop);
  }
  .canvas { position: relative; width: 1200px; height: 832px; }
  .plaque {
    position: absolute; left: 98px; top: 26px;
    width: 1003px; height: 780px;
    background: linear-gradient(135deg, var(--wood-light), var(--wood-mid) 45%, var(--wood-dark));
    border-radius: 4px;
  }
  .plate {
    position: absolute; left: 21px; top: 21px; right: 21px; bottom: 21px;
    background:
      repeating-linear-gradient(0deg, rgba(255,255,255,0.05) 0 1px, rgba(0,0,0,0.03) 1px 3px),
      linear-gradient(160deg, var(--brass-deep), var(--brass-light) 40%, var(--brass-mid) 65%, var(--brass-deep));
    box-shadow: inset 0 0 0 1px rgba(0,0,0,0.25);
  }
  .screw {
    position: absolute; width: 22px; height: 22px; border-radius: 50%;
    background: radial-gradient(circle at 35% 35%, var(--screw-light), var(--brass-mid) 45%, var(--screw-dark));
  }
  .screw.tl { left: 42px; top: 44px; }
  .screw.tr { right: 42px; top: 44px; }
  .screw.bl { left: 42px; bottom: 44px; }
  .screw.br { right: 42px; bottom: 44px; }
  .text {
    position: absolute; left: 87px; white-space: nowrap;
    font-family: "Arimo", Arial, sans-serif; color: var(--ink); line-height: 1.1;
  }
  .brand { top: 126px; font-size: 38px; font-weight: 700; letter-spacing: -0.5px; display: flex; align-items: center; gap: 10px; }
  .brand-mark { width: 18px; height: 18px; background: var(--ink); }
  .award-title { top: 201px; font-size: 42px; font-weight: 400; }
  .award-line { font-size: 34px; font-weight: 700; }
  .award-line.first { top: 253px; }
  .award-line.second { top: 300px; }
  .for { top: 346px; font-size: 24px; }
  .recipient { top: 382px; font-size: 31px; font-weight: 700; }
  .body { font-size: 22px; }
  .body.l1 { top: 424px; }
  .body.l2 { top: 459px; }
  .body.l3 { top: 494px; }
  .body.l4 { top: 529px; }
  .body .strong { font-weight: 700; }
  .body .small-bold { font-weight: 700; font-size: 16px; }
  .place-date { top: 646px; font-size: 22px; }
  .achiever {
    position: absolute; left: 532px; top: 85px; width: 352px; height: 582px;
  }
  .achiever-area { fill: var(--ink); }
</style>
</head>
<body>
<div class="canvas">
  <div class="plaque">
    <div class="plate">
      <span class="screw tl"></span>
      <span class="screw tr"></span>
      <span class="screw bl"></span>
      <span class="screw br"></span>

      <div class="text brand"><span>Kapitalwerk</span><span class="brand-mark"></span></div>
      <div class="text award-title">AUSZEICHNUNG</div>
      <div class="text award-line first">als herausragendster</div>
      <div class="text award-line second">Unternehmer Deutschlands 2013</div>
      <div class="text for">für</div>
      <div class="text recipient">Herrn Dipl.-Kfm. Max Muster</div>
      <div class="text body l1">Unter der Leitung von <span class="strong">Herr Dipl.-Kfm.</span> <span class="small-bold">Max Muster</span></div>
      <div class="text body l2">hat sich die FIRMA GmbH im Jahr 2013 unter</div>
      <div class="text body l3">den ersten 5% der größten deutschen</div>
      <div class="text body l4">Wirtschaftsunternehmen platziert.</div>
      <div class="text place-date">Gilching, 20. Juni 2013 Katrin Vollmer</div>

      <svg class="achiever" viewBox="0 0 352 582" role="img" aria-label="Silhouette einer jubelnden Person mit erhobenen Armen auf einem Siegerpodest">
        <path class="achiever-area" d="M44 0 H296 V141 H261 V459 H352 V582 H0 V459 H113 V141 H44 Z"/>
      </svg>
    </div>
  </div>
</div>
</body>
</html>
```